Harlow Mechanical Contractors needs a Website

Create basic website for commercial plumbing and mechanical contractor; to include pictures of works in progress and completed works, description of all services offered and geographical locations and licenses

Target Market(s)

General Contractors, Real Estate Developers, Construction Companies

Industry/Entity Type

Construction

Coding

Coded - Design and coding required

Number of Pages Required

5+ page

• See logo attached to project

Colors
0392cd

```html
<!DOCTYPE html>
<html lang="en">
<head>
<meta charset="utf-8">
<title>Harlow Mechanical Contractors</title>
<link rel="stylesheet" href="https://fonts.googleapis.com/css2?family=Raleway:wght@500;600;700;800&family=Open+Sans:wght@400;600;700&display=swap">
<style>
:root{
  --brand:#0392cd;
  --navy:#1c4a72;
  --navy-dark:#133552;
  --orange:#d0602b;
  --ink:#222;
  --text:#555;
  --line:#e3e3e3;
  --footer:#262626;
  --footer-line:#3c3c3c;
  --footer-text:#9a9a9a;
}
*{margin:0;padding:0;box-sizing:border-box}
html,body{width:698px;height:1200px;overflow:hidden;background:#fff}
body{position:relative;font-family:"Open Sans",sans-serif;color:var(--text)}
.abs{position:absolute}

/* header */
.brand{left:94px;top:22px;font-family:"Raleway",sans-serif;font-weight:600;font-size:11px;color:#333;white-space:nowrap}
.topbar{right:92px;top:11px;display:flex;gap:22px;font-size:6px;color:#a8a8a8}
.topbar span{display:flex;align-items:center;gap:5px}
.topbar b{font-weight:400;color:#777}
.header-rule{left:258px;top:30px;width:348px;height:1px;background:var(--line)}
.nav{top:43px;font-family:"Raleway",sans-serif;font-size:6.8px;font-weight:600;color:#333;letter-spacing:.3px}
.nav.active{color:var(--navy)}

/* hero */
.hero{left:0;top:62px;width:698px;height:287px;background:linear-gradient(90deg,#eef0f2 0%,#dde2e6 45%,#b9c7d8 65%,#3c63a0 85%,#2f4f86 100%)}
.hero-eyebrow{left:93px;top:171px;font-family:"Raleway",sans-serif;font-size:9.5px;font-weight:500;color:#222}
.hero-title{left:93px;top:185px;font-family:"Raleway",sans-serif;font-size:15px;font-weight:800;color:#111}
.hero-copy{left:93px;top:210px;width:180px;font-size:6.1px;line-height:9.6px;color:#333}
.btn{display:flex;align-items:center;justify-content:center;background:linear-gradient(#2b5f8e,var(--navy-dark));color:#fff;font-family:"Raleway",sans-serif;font-weight:700;font-size:5.8px;letter-spacing:.3px;box-shadow:0 1px 2px rgba(0,0,0,.3)}
.hero-btn{left:94px;top:261px;width:61px;height:22px}

/* section headings */
.sec-head,.svc-head{font-size:4.8px;line-height:6.5px}
.tag{display:inline-block;background:var(--orange);color:#fff;font-size:4.8px;padding:0 2px;line-height:6.5px;font-weight:600;vertical-align:top}
.sec-head{text-align:center;width:698px;left:0}
.sec-title{font-family:"Raleway",sans-serif;font-weight:800;font-size:11.5px;line-height:13px;color:var(--ink);margin-top:1px}

/* about */
.about-frame{left:100px;top:429px;width:242px;height:102px;background:#e5ebee}
.about-photo{left:119px;top:414px;width:205px;height:132px;background:linear-gradient(135deg,#d6dbe0,#8b949c 55%,#3d4246)}
.about-copy{left:365px;top:427px;width:232px;font-size:5.9px;line-height:11.8px;color:#555}
.about-btn{left:365px;top:512px;width:55px;height:19px}
.divider{left:94px;width:512px;height:1px;background:var(--line)}

/* services */
.svc-head{left:99px;top:599px}
.svc-icon{width:30px;height:29px;display:flex;align-items:center;justify-content:center;border:1px solid #555}
.svc-icon.filled{background:linear-gradient(#2b5f8e,var(--navy-dark));border:none}
.svc-title{font-family:"Raleway",sans-serif;font-size:9px;font-weight:500;color:#222}
.svc-text{font-size:6px;line-height:10.4px;color:#666;width:112px;margin-top:3px}

/* blog */
.card{top:771px;width:115px;height:123px;border:1px solid #e4e4e4;background:#fff}
.card-img{height:67px;background:linear-gradient(135deg,#c9a25a,#6b5a42 50%,#2f2c2a)}
.card-img.b{background:linear-gradient(135deg,#e6e8ea,#9aa1a6 55%,#7b3a34)}
.card-img.c{background:linear-gradient(135deg,#eef0f2,#b4bcc4 50%,#b3382e)}
.card-img.d{background:linear-gradient(135deg,#e9eaeb,#bfc2c4 55%,#a87040)}
.date{position:absolute;left:8px;top:9px;width:14px;height:14px;background:#111;color:#fff;font-size:3px;line-height:4px;text-align:center;padding-top:3px;font-weight:700}
.card-body{padding:10px 5px 0 5px}
.card-title{font-family:"Raleway",sans-serif;font-size:6.2px;font-weight:700;color:#111}
.card-text{font-size:4.6px;line-height:10.2px;color:#999;margin-top:2px}
.card-text a{color:var(--brand);font-weight:700;text-decoration:none}

/* cta */
.cta{left:0;top:914px;width:698px;height:62px;background:linear-gradient(#2c6c99,#1f4f78 60%,#163d60)}
.cta-title{left:114px;top:926px;font-family:"Raleway",sans-serif;font-size:12px;font-weight:500;color:#fff}
.cta-copy{left:114px;top:942px;width:362px;font-size:6.6px;line-height:9.6px;color:#fff}
.cta-copy b{font-size:8px;font-weight:700}
.cta-btn{left:492px;top:934px;width:80px;height:23px;background:linear-gradient(#d9692f,#b94f1d);color:#fff;font-family:"Raleway",sans-serif;font-weight:700;font-size:6.4px;display:flex;align-items:center;justify-content:center;letter-spacing:.3px}

/* footer */
.footer{left:0;top:976px;width:698px;height:224px;background:var(--footer)}
.f-head{top:1015px;font-family:"Raleway",sans-serif;font-weight:800;font-size:7px;color:#fff}
.f-head::after{content:"";display:block;width:15px;height:1px;background:var(--brand);margin-top:6px;opacity:.8}
.f-link{width:71px;font-family:"Raleway",sans-serif;font-size:5.4px;font-weight:600;color:#cfcfcf;letter-spacing:.3px;padding-bottom:5px;border-bottom:1px solid var(--footer-line)}
.f-link.last{border-bottom:none}
.f-text{font-size:5.6px;line-height:10.4px;color:var(--footer-text)}
.f-text strong{color:#fff;font-weight:600}
.f-label{font-family:"Raleway",sans-serif;font-weight:700;font-size:5.6px;color:#fff}
.f-input{left:442px;top:1086px;width:132px;height:20px;background:#333;border:1px solid #3d3d3d;font-size:5.8px;color:#999;padding-left:8px;display:flex;align-items:center}
.f-send{left:574px;top:1086px;width:24px;height:20px;background:var(--orange);display:flex;align-items:center;justify-content:center}
.copyright{left:101px;top:1162px;font-size:5.6px;color:#8a8a8a}
.bottom-bar{left:350px;top:1160px;width:348px;height:22px}
.bottom-links{left:377px;top:1166px;display:flex;gap:12px;font-size:5.6px;color:#9a9a9a}
</style>
</head>
<body>

<!-- header -->
<div class="abs brand">Harlow Mechanical Contractors</div>
<div class="abs topbar">
  <span><svg width="7" height="6" viewBox="0 0 7 6"><rect width="7" height="6" fill="#1c4a72"/><path d="M0 0L3.5 3L7 0" stroke="#fff" stroke-width=".7" fill="none"/></svg>Mail Us : <b>office@harlowmech.com</b></span>
  <span><svg width="6" height="6" viewBox="0 0 6 6"><path d="M1 0L2.3 1.6L1.6 2.4Q2.4 3.8 3.6 4.4L4.4 3.7L6 5L5 6Q1.5 5.5 0 1Z" fill="#1c4a72"/></svg>Call Us : 9855 210 3370</span>
</div>
<div class="abs header-rule"></div>
<div class="abs nav active" style="left:317px">HOME</div>
<div class="abs nav" style="left:359px">ABOUT US</div>
<div class="abs nav" style="left:417px">CONTACT</div>
<div class="abs nav" style="left:470px">PRODUCTS &amp; SERVICES</div>
<div class="abs nav" style="left:570px">SUPPORT</div>

<!-- hero -->
<div class="abs hero" role="img" aria-label="Smiling plumber in a blue cap and overalls leaning on a kitchen sink with exposed pipes"></div>
<svg class="abs" style="left:28px;top:176px" width="17" height="36" viewBox="0 0 17 36"><path d="M16 1L1 18L16 35" stroke="#fff" stroke-width="1" fill="none"/></svg>
<svg class="abs" style="left:665px;top:186px" width="8" height="16" viewBox="0 0 8 16"><path d="M1 1L7 8L1 15" stroke="#fff" stroke-width="1" fill="none"/></svg>
<div class="abs hero-eyebrow">LOREM IPSUM DOLOR</div>
<div class="abs hero-title">WELCOME TO OUR SITE</div>
<p class="abs hero-copy">Praesent id nisi at velit aliquam tincidunt quis sed tellus. Duis metus nibh, dictum vitae metus nec, tristique tincidunt lacus. Suspendisse ultrices feugiat nunc ut egestas. In hac habitasse platea dictumst.</p>
<div class="abs btn hero-btn">CONTACT US</div>

<!-- about -->
<div class="abs sec-head" style="top:376px"><span class="tag">LOREM</span><div class="sec-title">ABOUT US</div></div>
<div class="abs about-frame"></div>
<div class="abs about-photo" role="img" aria-label="Hands tightening under-sink pipes with a red pipe wrench"></div>
<p class="abs about-copy">Lorem ipsum dolor sit amet, consectetur adipiscing elit. Donec luctus arcu nisi, sed malesuada felis tristique eu. Phasellus eget tincidunt orci. In felis dolor, convallis non tortor eu, egestas pharetra metus. Nulla eu neque ac turpis mollis malesuada. Suspendisse potenti. Praesent fringilla massa eget aliquet cursus. Morbi eu leo auctor, euismod odio in, luctus ipsum. Aenean et tellus justo. Nullam vulputate vel dui non posuere. In ac accumsan magna, non</p>
<div class="abs btn about-btn">READ MORE</div>
<div class="abs divider" style="top:574px"></div>

<!-- service areas -->
<div class="abs svc-head"><span class="tag">OUR</span><div class="sec-title">SERVICE AREAS</div></div>
<div class="abs svc-icon filled" style="left:100px;top:641px"><svg width="9" height="11" viewBox="0 0 9 11"><rect x=".5" y=".5" width="8" height="10" fill="none" stroke="#fff" stroke-width=".8"/><path d="M2.5 3h1M5.5 3h1M2.5 5h1M5.5 5h1M2.5 7h1M5.5 7h1" stroke="#fff" stroke-width=".8"/></svg></div>
<div class="abs" style="left:142px;top:639px"><div class="svc-title">For large offices</div><p class="svc-text">Lorem Ipsum is simply dummy text of the printing and typesetting industry. Lorem Ipsum has been.</p></div>
<div class="abs svc-icon" style="left:270px;top:641px"><svg width="14" height="10" viewBox="0 0 14 10"><path d="M1 4L4 1L7 3L10 1L13 4L7 9Z" fill="none" stroke="#333" stroke-width=".8"/><path d="M4 5L6 7M6 4L8 6" stroke="#333" stroke-width=".7"/></svg></div>
<div class="abs" style="left:313px;top:639px"><div class="svc-title">Condominiums</div><p class="svc-text">Lorem Ipsum is simply dummy text of the printing and typesetting industry. Lorem Ipsum has been.</p></div>
<div class="abs svc-icon" style="left:452px;top:641px"><svg width="12" height="12" viewBox="0 0 12 12"><circle cx="4.5" cy="7" r="2.6" fill="none" stroke="#333" stroke-width="1.2" stroke-dasharray="1.2 .8"/><circle cx="4.5" cy="7" r=".9" fill="#333"/><circle cx="9" cy="3" r="1.8" fill="none" stroke="#333" stroke-width="1" stroke-dasharray="1 .7"/></svg></div>
<div class="abs" style="left:494px;top:639px"><div class="svc-title">Industrial projects</div><p class="svc-text">Lorem Ipsum is simply dummy text of the printing and typesetting industry. Lorem Ipsum has been.</p></div>
<div class="abs divider" style="top:711px"></div>

<!-- blog -->
<div class="abs sec-head" style="top:737px"><span class="tag">LATEST</span><div class="sec-title">BLOG</div></div>
<div class="abs card" style="left:100px"><div class="card-img" role="img" aria-label="Assorted hand tools: hammer, tape measure and wrenches"></div><div class="date">17<br>MAR</div><div class="card-body"><div class="card-title">Blog Post Title Here</div><p class="card-text">It is a long established fact that a reader will be distracted by the readable content of a page when looking at its layout. <a>Read More</a></p></div></div>
<div class="abs card" style="left:228px"><div class="card-img b" role="img" aria-label="Plumber working on sink drain pipes"></div><div class="date">18<br>MAR</div><div class="card-body"><div class="card-title">Blog Post Title Here</div><p class="card-text">It is a long established fact that a reader will be distracted by the readable content of a page when looking at its layout. <a>Read More</a></p></div></div>
<div class="abs card" style="left:355px"><div class="card-img c" role="img" aria-label="Pipe wrenches and pliers on a white surface"></div><div class="date">12<br>FEB</div><div class="card-body"><div class="card-title">Blog Post Title Here</div><p class="card-text">It is a long established fact that a reader will be distracted by the readable content of a page when looking at its layout. <a>Read More</a></p></div></div>
<div class="abs card" style="left:483px"><div class="card-img d" role="img" aria-label="Copper fittings and a wrench resting on floor plans"></div><div class="date">24<br>JAN</div><div class="card-body"><div class="card-title">Blog Post Title Here</div><p class="card-text">It is a long established fact that a reader will be distracted by the readable content of a page when looking at its layout. <a>Read More</a></p></div></div>

<!-- call to action -->
<div class="abs cta"></div>
<div class="abs cta-title">Want Our Service?</div>
<p class="abs cta-copy"><b>Lorem ipsum dolor sit amet</b>, consectetur adipiscing elit. Donec suscipit sed arcu in finibus. Quisque at tincidunt ipsum, id mollis lectus. Nam sit amet venenatis magna.</p>
<div class="abs cta-btn">CONTACT NOW</div>

<!-- footer -->
<div class="abs footer"></div>
<div class="abs f-head" style="left:101px">QUICK LINKS</div>
<div class="abs f-head" style="left:294px">CONTACT US</div>
<div class="abs f-head" style="left:442px">NEWSLETTER SIGNUP</div>

<div class="abs f-link" style="left:102px;top:1053px">HOME</div>
<div class="abs f-link" style="left:102px;top:1071px">PRODUCTS</div>
<div class="abs f-link" style="left:102px;top:1090px">QUALITY</div>
<div class="abs f-link last" style="left:102px;top:1108px">FAQ</div>
<div class="abs f-link" style="left:186px;top:1053px">ABOUT US</div>
<div class="abs f-link" style="left:186px;top:1071px">CONTACT US</div>
<div class="abs f-link" style="left:186px;top:1090px">JOBS</div>
<div class="abs f-link last" style="left:186px;top:1108px">TERMS &amp; CONDITIONS</div>

<div class="abs f-label" style="left:293px;top:1052px">LOCATION</div>
<p class="abs f-text" style="left:293px;top:1061px">1580 Cedar Ridge Road<br>Millbrook, UT 84090</p>
<p class="abs f-text" style="left:293px;top:1093px"><strong>Phone :</strong> (801) 555-0142<br><strong>Email :</strong> info@harlowmech.com</p>

<p class="abs f-text" style="left:442px;top:1051px;width:160px">If you want receive our all weekly updates about new offers and discount, signup below.</p>
<div class="abs f-input">Email Address</div>
<div class="abs f-send"><svg width="8" height="8" viewBox="0 0 8 8"><path d="M0 3.5L8 0L5 8L4 4.5Z" fill="#fff"/></svg></div>

<div class="abs copyright">Copyright © 2016. harlowmech All Rights Reserved</div>
<svg class="abs bottom-bar" viewBox="0 0 348 22" preserveAspectRatio="none"><path d="M14 0H348V22H0Z" fill="#2f2f2f"/></svg>
<div class="abs bottom-links"><span>Terms of Use</span><span>Legal Desclaimer</span><span>Privacy Policy</span><span>Support</span><span>Sitemap</span></div>

</body>
</html>
```